Spiritual Healing bussiness needs logo/business card

Simple, clean looking logo/card
For spiritual business with healing services and occult rituals

Contact Information for Business Card

Needs my name: Tobin Varley
Business name: Lantern Healing Shop
Services provided and worded in this way:

Reiki Healing
Tarot
Oils
Rituals Of Change

Can look occult like but with light energy.

Colors
0255a3
3276b5
85abd2
33a6d7
85cae6
0292cd

```html
<!DOCTYPE html>
<html lang="en">
<head>
<meta charset="utf-8">
<title>Lantern Healing Shop – Business Card</title>
<link href="https://fonts.googleapis.com/css2?family=Work+Sans:wght@400;500&family=Oswald:wght@500&display=swap" rel="stylesheet">
<style>
  :root {
    --backdrop: #1a1a1a;
    --card: #232323;
    --card-edge: #2b2b2b;
    --blue: #0255a3;
    --blue-icon: #3276b5;
    --white: #f2f2f2;
    --pale: #c8c8c8;
  }
  * { margin: 0; padding: 0; box-sizing: border-box; }
  html, body { width: 1200px; height: 900px; overflow: hidden; }
  body {
    background: var(--backdrop);
    font-family: "Work Sans", Arial, sans-serif;
    position: relative;
  }
  .card {
    position: absolute;
    left: 250px;
    width: 700px;
    height: 400px;
    background: linear-gradient(135deg, var(--card) 0%, var(--card) 60%, var(--card-edge) 100%);
    color: var(--white);
  }
  .card--front { top: 30px; }
  .card--back { top: 470px; }

  .front__name {
    position: absolute;
    top: 168px; left: 0; width: 100%;
    text-align: center;
    font-weight: 500;
    font-size: 30px;
    letter-spacing: 7px;
    text-transform: uppercase;
    color: var(--pale);
  }
  .front__services {
    position: absolute;
    bottom: 52px; left: 0; width: 100%;
    text-align: center;
    font-size: 17px;
    letter-spacing: 0.5px;
  }
  .front__services .sep { color: var(--blue); margin: 0 8px; }

  .back__brand {
    position: absolute;
    top: 60px; left: 0; width: 100%;
    text-align: center;
    font-weight: 500;
    font-size: 26px;
    letter-spacing: 6px;
    text-transform: uppercase;
    color: var(--white);
  }
  .back__person {
    position: absolute;
    top: 148px; right: 384px;
    text-align: right;
  }
  .back__person-name {
    font-family: "Oswald", "Arial Narrow", sans-serif;
    font-weight: 500;
    font-size: 44px;
    letter-spacing: 2px;
    color: var(--blue);
    text-transform: uppercase;
    line-height: 1.1;
  }
  .back__person-role { font-size: 19px; letter-spacing: 0.5px; }
  .back__rule {
    position: absolute;
    top: 160px; left: 340px;
    width: 2px; height: 72px;
    background: var(--blue);
  }
  .back__contacts {
    position: absolute;
    top: 158px; left: 364px;
    list-style: none;
    font-size: 19px;
    line-height: 27px;
    letter-spacing: 0.3px;
  }
  .back__contacts li { display: flex; align-items: center; gap: 10px; }
  .back__contacts svg { width: 12px; height: 12px; flex: none; }
  .back__address {
    position: absolute;
    bottom: 56px; left: 0; width: 100%;
    text-align: center;
    font-size: 20px;
    letter-spacing: 0.5px;
  }
</style>
</head>
<body>

<section class="card card--front">
  <h1 class="front__name">Lantern Healing Shop</h1>
  <p class="front__services">Reiki Healing<span class="sep">|</span>Tarot<span class="sep">|</span>Oils<span class="sep">|</span>Rituals Of Change</p>
</section>

<section class="card card--back">
  <h2 class="back__brand">Lantern Healing Shop</h2>
  <div class="back__person">
    <p class="back__person-name">Tobin Varley</p>
    <p class="back__person-role">Director</p>
  </div>
  <div class="back__rule"></div>
  <ul class="back__contacts">
    <li>
      <svg viewBox="0 0 12 12" aria-hidden="true"><path d="M2.5 1 L4.5 1 L5 3.5 L3.8 4.4 Q4.8 6.8 7.6 8.2 L8.5 7 L11 7.5 L11 9.5 Q11 11 9.5 11 Q1 10 1 2.5 Q1 1 2.5 1 Z" fill="var(--blue-icon)"/></svg>
      (555) 614-2097
    </li>
    <li>
      <svg viewBox="0 0 12 12" aria-hidden="true"><rect x="1" y="2.5" width="10" height="7" fill="none" stroke="var(--blue-icon)" stroke-width="1.2"/><path d="M1 2.5 L6 6.5 L11 2.5" fill="none" stroke="var(--blue-icon)" stroke-width="1.2"/></svg>
      hello@lanternhealingshop.com
    </li>
    <li>
      <svg viewBox="0 0 12 12" aria-hidden="true"><g fill="none" stroke="var(--blue-icon)" stroke-width="1"><circle cx="6" cy="6" r="5"/><ellipse cx="6" cy="6" rx="2.2" ry="5"/><path d="M1 6 H11"/></g></svg>
      www.lanternhealingshop.com
    </li>
  </ul>
  <p class="back__address">48b Larch Lane, Westbrook, NZ, 4120</p>
</section>

</body>
</html>
```